Billiards 50th Anniversary Calendar

Need a custom calendar designed to finish at 8.5 x 11. and to be supplied as a pdf print file including .25 bleed on all sides. Total is 24 pages. I will supply one image per calendar month. Cover to have a collage of monthly images or samples of some of your favorites incorporated with a cool design that transitions throughout the calendar. The client's 50th Anniversary logo must be incorporated into the design.

Back cover has a group image to be incorporated as well.

Target Market(s)

Calendar is selling to their billiard clients

Industry/Entity Type

Male dominant industry

Requirements
Must have
• Must have a design element that continues through the calendar but flows with the images well. One image per calendar month.

```html
<!DOCTYPE html>
<html lang="en">
<head>
<meta charset="utf-8">
<title>Cue Corner Billiards 50th Anniversary Calendar – July to December 2022</title>
<link href="https://fonts.googleapis.com/css2?family=Questrial&family=Montserrat:wght@700&display=swap" rel="stylesheet">
<style>
  :root{
    --paper:#ffffff;
    --ink:#3a3a3a;
    --green:#14923f;
    --orange:#ef7f1f;
    --red:#e3202b;
    --rule:#c9c9c9;
    --head-grey:#d4d4d4;
    --felt:#1d8fd6;
    --night:#141414;
  }
  *{box-sizing:border-box;margin:0;padding:0}
  html,body{width:1200px;height:923px;overflow:hidden;background:var(--paper)}
  body{position:relative;font-family:"Questrial",sans-serif;color:var(--ink)}

  .page{position:absolute;width:258px;height:399px;background:var(--paper)}
  .page--jul{left:55.5px;top:50px}
  .page--aug{left:332.5px;top:50px}
  .page--sep{left:609.5px;top:50px}
  .page--oct{left:55.5px;top:474.7px}
  .page--nov{left:332.5px;top:474.7px}
  .page--dec{left:609.5px;top:474.7px}

  .photo{position:absolute;left:0;top:0;width:258px;height:199px}
  .photo--felt{background:radial-gradient(ellipse at 50% 80%,#2a9be0 0%,#1873b3 35%,#1c1512 75%,#0d0a09 100%)}
  .photo--night{background:radial-gradient(ellipse at 50% 45%,#6b3a34 0%,#2a1a18 40%,#0d0c0c 80%),#0d0c0c}
  .photo--brick{background:linear-gradient(180deg,#7a3b2c 0%,#5b2a20 55%,#d8c2a0 62%,#cdb48e 100%)}
  .photo--top{background:linear-gradient(180deg,#2a1c16 0%,#2396d8 8%,#1f8ccd 60%,#2396d8 92%,#2a1c16 100%)}

  .month-title{position:absolute;left:0;top:205px;width:258px;text-align:center;font-size:17.5px;line-height:20px;letter-spacing:-0.3px}
  .month-title .year{color:var(--ink)}
  .month-title--green .name{color:var(--green)}
  .month-title--orange .name{color:var(--orange)}

  .brand{position:absolute;right:16px;top:204px;width:28px;text-align:center;font-family:"Montserrat",sans-serif;font-weight:700;font-size:5px;line-height:6px;color:var(--green)}
  .brand .dot{display:block;width:9px;height:9px;margin:0 auto 2px;border-radius:50%;background:var(--orange)}

  .grid{position:absolute;left:7.7px;top:230px;width:242.8px;border-collapse:collapse;table-layout:fixed}
  .grid th{height:6.2px;font-size:2.6px;font-family:"Montserrat",sans-serif;font-weight:700;letter-spacing:.1px;background:var(--head-grey);color:#555;border:0.5px solid #fff;text-transform:uppercase}
  .grid th.sun{background:var(--red);color:#fff}
  .grid td{height:30.1px;border:0.6px solid var(--rule);vertical-align:top;text-align:right;padding:1px 3px 0 0;font-size:7.6px;color:var(--ink);position:relative}
  .grid td.sun{color:var(--red)}
  .grid td.split{background:linear-gradient(to top right,transparent calc(50% - .4px),var(--rule) 50%,transparent calc(50% + .4px))}
  .grid td.split .low{position:absolute;left:2px;bottom:1px}

  .band{position:absolute;left:0;top:394.5px;width:258px;height:4.4px}
  .band--orange{background:var(--orange)}
  .band--green{background:var(--green)}

  .back-cover{position:absolute;left:886.3px;top:673.7px;width:258.3px;height:199.5px;background:linear-gradient(180deg,#3a1f1a 0%,#4a2a20 45%,#8a4a22 75%,#c8692a 100%)}
  .back-cover .photo{height:199.5px;width:258.3px;background:radial-gradient(ellipse at 50% 40%,rgba(150,70,60,.55) 0%,rgba(60,30,25,0) 70%)}
  .back-brand{position:absolute;left:104px;top:140px;width:80px;text-align:center;font-family:"Montserrat",sans-serif;font-weight:700;font-size:8px;line-height:9px;color:#f3c22a}
  .back-brand .dot{display:block;width:14px;height:14px;margin:0 auto 3px;border-radius:50%;background:#f3c22a}
</style>
</head>
<body>

<!-- JULY -->
<section class="page page--jul">
  <div class="photo photo--felt" role="img" aria-label="Pin-up model in a floral dress and red sunglasses lying across a blue pool table"></div>
  <h2 class="month-title month-title--green"><span class="name">JULY</span><span class="year">2022</span></h2>
  <div class="brand"><span class="dot"></span>CUE CORNER</div>
  <table class="grid">
    <tr><th class="sun">Sunday</th><th>Monday</th><th>Tuesday</th><th>Wednesday</th><th>Thursday</th><th>Friday</th><th>Saturday</th></tr>
    <tr><td class="sun"></td><td></td><td></td><td></td><td></td><td>1</td><td>2</td></tr>
    <tr><td class="sun">3</td><td>4</td><td>5</td><td>6</td><td>7</td><td>8</td><td>9</td></tr>
    <tr><td class="sun">10</td><td>11</td><td>12</td><td>13</td><td>14</td><td>15</td><td>16</td></tr>
    <tr><td class="sun">17</td><td>18</td><td>19</td><td>20</td><td>21</td><td>22</td><td>23</td></tr>
    <tr><td class="sun split">24<span class="low">31</span></td><td>25</td><td>26</td><td>27</td><td>28</td><td>29</td><td>30</td></tr>
  </table>
  <div class="band band--orange"></div>
</section>

<!-- AUGUST -->
<section class="page page--aug">
  <div class="photo photo--night" role="img" aria-label="Pin-up model in a red dress holding a cue, seated on a blue pool table"></div>
  <h2 class="month-title month-title--orange"><span class="name">AUGUST</span><span class="year">2022</span></h2>
  <div class="brand"><span class="dot"></span>CUE CORNER</div>
  <table class="grid">
    <tr><th class="sun">Sunday</th><th>Monday</th><th>Tuesday</th><th>Wednesday</th><th>Thursday</th><th>Friday</th><th>Saturday</th></tr>
    <tr><td class="sun"></td><td>1</td><td>2</td><td>3</td><td>4</td><td>5</td><td>6</td></tr>
    <tr><td class="sun">7</td><td>8</td><td>9</td><td>10</td><td>11</td><td>12</td><td>13</td></tr>
    <tr><td class="sun">14</td><td>15</td><td>16</td><td>17</td><td>18</td><td>19</td><td>20</td></tr>
    <tr><td class="sun">21</td><td>22</td><td>23</td><td>24</td><td>25</td><td>26</td><td>27</td></tr>
    <tr><td class="sun">28</td><td>29</td><td>30</td><td>31</td><td></td><td></td><td></td></tr>
  </table>
  <div class="band band--green"></div>
</section>

<!-- SEPTEMBER -->
<section class="page page--sep">
  <div class="photo photo--brick" role="img" aria-label="Pin-up model in a polka-dot rose dress reclining on a counter in front of a framed brick wall"></div>
  <h2 class="month-title month-title--green"><span class="name">SEPTEMBER</span><span class="year">2022</span></h2>
  <div class="brand"><span class="dot"></span>CUE CORNER</div>
  <table class="grid">
    <tr><th class="sun">Sunday</th><th>Monday</th><th>Tuesday</th><th>Wednesday</th><th>Thursday</th><th>Friday</th><th>Saturday</th></tr>
    <tr><td class="sun"></td><td></td><td></td><td></td><td>1</td><td>2</td><td>3</td></tr>
    <tr><td class="sun">4</td><td>5</td><td>6</td><td>7</td><td>8</td><td>9</td><td>10</td></tr>
    <tr><td class="sun">11</td><td>12</td><td>13</td><td>14</td><td>15</td><td>16</td><td>17</td></tr>
    <tr><td class="sun">18</td><td>19</td><td>20</td><td>21</td><td>22</td><td>23</td><td>24</td></tr>
    <tr><td class="sun">25</td><td>26</td><td>27</td><td>28</td><td>29</td><td>30</td><td></td></tr>
  </table>
  <div class="band band--orange"></div>
</section>

<!-- OCTOBER -->
<section class="page page--oct">
  <div class="photo photo--top" role="img" aria-label="Overhead view of a pin-up model in a black floral dress lying among balls on a blue pool table"></div>
  <h2 class="month-title month-title--orange"><span class="name">OCTOBER</span><span class="year">2022</span></h2>
  <div class="brand"><span class="dot"></span>CUE CORNER</div>
  <table class="grid">
    <tr><th class="sun">Sunday</th><th>Monday</th><th>Tuesday</th><th>Wednesday</th><th>Thursday</th><th>Friday</th><th>Saturday</th></tr>
    <tr><td class="sun"></td><td></td><td></td><td></td><td></td><td></td><td>1</td></tr>
    <tr><td class="sun">2</td><td>3</td><td>4</td><td>5</td><td>6</td><td>7</td><td>8</td></tr>
    <tr><td class="sun">9</td><td>10</td><td>11</td><td>12</td><td>13</td><td>14</td><td>15</td></tr>
    <tr><td class="sun">16</td><td>17</td><td>18</td><td>19</td><td>20</td><td>21</td><td>22</td></tr>
    <tr><td class="sun split">23<span class="low">30</span></td><td class="split">24<span class="low">31</span></td><td>25</td><td>26</td><td>27</td><td>28</td><td>29</td></tr>
  </table>
  <div class="band band--green"></div>
</section>

<!-- NOVEMBER -->
<section class="page page--nov">
  <div class="photo photo--felt" role="img" aria-label="Pin-up model in a polka-dot outfit lying on a pool table with balls in front"></div>
  <h2 class="month-title month-title--green"><span class="name">NOVEMBER</span><span class="year">2022</span></h2>
  <div class="brand"><span class="dot"></span>CUE CORNER</div>
  <table class="grid">
    <tr><th class="sun">Sunday</th><th>Monday</th><th>Tuesday</th><th>Wednesday</th><th>Thursday</th><th>Friday</th><th>Saturday</th></tr>
    <tr><td class="sun"></td><td></td><td>1</td><td>2</td><td>3</td><td>4</td><td>5</td></tr>
    <tr><td class="sun">6</td><td>7</td><td>8</td><td>9</td><td>10</td><td>11</td><td>12</td></tr>
    <tr><td class="sun">13</td><td>14</td><td>15</td><td>16</td><td>17</td><td>18</td><td>19</td></tr>
    <tr><td class="sun">20</td><td>21</td><td>22</td><td>23</td><td>24</td><td>25</td><td>26</td></tr>
    <tr><td class="sun">27</td><td>28</td><td>29</td><td>30</td><td></td><td></td><td></td></tr>
  </table>
  <div class="band band--orange"></div>
</section>

<!-- DECEMBER -->
<section class="page page--dec">
  <div class="photo photo--night" role="img" aria-label="Flapper-style model with feather headband seated on a pool table wrapped in a sheer robe"></div>
  <h2 class="month-title month-title--orange"><span class="name">DECEMBER</span><span class="year">2022</span></h2>
  <div class="brand"><span class="dot"></span>CUE CORNER</div>
  <table class="grid">
    <tr><th class="sun">Sunday</th><th>Monday</th><th>Tuesday</th><th>Wednesday</th><th>Thursday</th><th>Friday</th><th>Saturday</th></tr>
    <tr><td class="sun"></td><td></td><td></td><td></td><td>1</td><td>2</td><td>3</td></tr>
    <tr><td class="sun">4</td><td>5</td><td>6</td><td>7</td><td>8</td><td>9</td><td>10</td></tr>
    <tr><td class="sun">11</td><td>12</td><td>13</td><td>14</td><td>15</td><td>16</td><td>17</td></tr>
    <tr><td class="sun">18</td><td>19</td><td>20</td><td>21</td><td>22</td><td>23</td><td>24</td></tr>
    <tr><td class="sun">25</td><td>26</td><td>27</td><td>28</td><td>29</td><td>30</td><td>31</td></tr>
  </table>
  <div class="band band--green"></div>
</section>

<!-- BACK COVER -->
<section class="back-cover">
  <div class="photo" role="img" aria-label="Group photo of the calendar models gathered at the billiard hall bar"></div>
  <div class="back-brand"><span class="dot"></span>CUE CORNER<br>50 YEARS</div>
</section>

</body>
</html>
```